Business Card Design

Attached is my current Business card I do not like it but I must save the logo portion of it. Don't like the color or the lettering am looking for more architectural look in grays or taupe with the green more of a charturese color and the blue a charcoal color on a textured paper that looks more like something high-end that would appeal to an architect or a designer. We make concrete decorative items such as concrete fireplaces, sinks, tops and more.

Target Market(s)

Architects designers of Commercial and Residential - artistic features

Industry/Entity Type

Architect

Contact Information for Business Card

Marisol T. Quenby President and Marketing Director
602-418-5093
email marisol@vantorelstone.example
Showroom "Quillmont Design Center" 4183 W Palomar Scottsdale AZ
Fax: 602-731-6624

Font styles to use
Sans Serif

Requirements
Must have
• Architectural
Natural and earthy colors with a touch of color in the existing attached

```html
<!DOCTYPE html>
<html lang="en">
<head>
<meta charset="utf-8">
<title>Vantorel Stone Business Card</title>
<link rel="stylesheet" href="https://fonts.googleapis.com/css2?family=Titillium+Web:wght@300;400;600&display=swap">
<style>
  :root {
    --bg: #e9e7e3;
    --taupe: #777264;
    --charcoal: #36495e;
    --chartreuse: #9bb72c;
    --paper: #f1f1f0;
    --ink: #3b3d40;
    --light: #f4f3ef;
  }
  * { box-sizing: border-box; margin: 0; padding: 0; }
  html, body { width: 1200px; height: 1000px; overflow: hidden; }
  body {
    background: var(--bg);
    font-family: "Titillium Web", sans-serif;
    position: relative;
  }
  .card {
    position: absolute;
    left: 240px;
    width: 720px;
    height: 411px;
    overflow: hidden;
    box-shadow: 0 6px 18px rgba(0,0,0,0.15);
  }
  .card--brand { top: 50px; background: var(--taupe); }
  .card--contact { top: 535px; background: var(--paper); }

  .brand-mark {
    display: flex;
    align-items: center;
    gap: 12px;
  }
  .brand-mark__square {
    width: 22px; height: 22px;
    background: var(--chartreuse);
  }
  .brand-mark__name {
    font-weight: 300;
    letter-spacing: 2px;
    text-transform: uppercase;
  }
  .brand-tagline {
    font-weight: 300;
    text-align: right;
  }

  .card--brand .brand-block {
    position: absolute;
    left: 50%; top: 50%;
    transform: translate(-50%, -50%);
  }
  .card--brand .brand-mark__name { font-size: 30px; color: var(--light); }
  .card--brand .brand-tagline { font-size: 17px; color: var(--light); }

  .contact-top {
    position: absolute; left: 0; top: 0; width: 720px; height: 190px;
    background: var(--paper);
  }
  .contact-top .brand-block {
    position: absolute; left: 50%; top: 95px;
    transform: translate(-50%, -50%);
  }
  .contact-top .brand-mark__name { font-size: 28px; color: var(--ink); }
  .contact-top .brand-tagline { font-size: 16px; color: var(--ink); }

  .accent-band {
    position: absolute; left: 0; top: 190px; width: 720px; height: 24px;
    background: var(--charcoal);
  }
  .identity-panel {
    position: absolute; left: 0; top: 214px; width: 470px; height: 197px;
    background: var(--taupe);
    color: var(--light);
  }
  .identity-panel__name {
    position: absolute; right: 28px; top: 22px;
    font-size: 46px; font-weight: 300; letter-spacing: 1px;
  }
  .identity-panel__title {
    position: absolute; right: 28px; top: 86px;
    font-size: 17px; font-weight: 300;
  }
  .identity-panel .brand-block {
    position: absolute; left: 26px; bottom: 22px;
  }
  .identity-panel .brand-mark { gap: 8px; }
  .identity-panel .brand-mark__square { width: 14px; height: 14px; background: var(--light); }
  .identity-panel .brand-mark__name { font-size: 16px; color: var(--light); letter-spacing: 1px; }
  .identity-panel .brand-tagline { font-size: 11px; color: var(--light); }

  .contact-list {
    position: absolute; left: 470px; top: 214px; width: 250px; height: 106px;
    background: var(--paper);
    padding: 16px 0 0 18px;
    list-style: none;
    color: var(--ink);
    font-size: 14px;
    line-height: 24px;
  }
  .contact-list li { display: flex; align-items: center; gap: 8px; }
  .contact-list svg { width: 12px; height: 12px; fill: var(--ink); flex: none; }

  .showroom {
    position: absolute; left: 470px; top: 320px; width: 250px; height: 91px;
    background: var(--chartreuse);
    padding: 12px 0 0 18px;
    color: var(--ink);
    font-size: 13px;
    line-height: 20px;
  }
  .showroom__label { font-weight: 600; }
</style>
</head>
<body>

<section class="card card--brand">
  <div class="brand-block">
    <div class="brand-mark">
      <span class="brand-mark__square"></span>
      <span class="brand-mark__name">Vantorel Stone</span>
    </div>
    <div class="brand-tagline">Design Studio</div>
  </div>
</section>

<section class="card card--contact">
  <div class="contact-top">
    <div class="brand-block">
      <div class="brand-mark">
        <span class="brand-mark__square"></span>
        <span class="brand-mark__name">Vantorel Stone</span>
      </div>
      <div class="brand-tagline">Design Studio</div>
    </div>
  </div>

  <div class="accent-band"></div>

  <div class="identity-panel">
    <h1 class="identity-panel__name">Marisol T. Quenby</h1>
    <p class="identity-panel__title">President &amp; Marketing Director</p>
    <div class="brand-block">
      <div class="brand-mark">
        <span class="brand-mark__square"></span>
        <span class="brand-mark__name">Vantorel Stone</span>
      </div>
      <div class="brand-tagline">Design Studio</div>
    </div>
  </div>

  <ul class="contact-list">
    <li>
      <svg viewBox="0 0 24 24" aria-hidden="true"><path d="M6.6 10.8a15.1 15.1 0 0 0 6.6 6.6l2.2-2.2a1 1 0 0 1 1-.25 11.4 11.4 0 0 0 3.6.57 1 1 0 0 1 1 1V20a1 1 0 0 1-1 1A17 17 0 0 1 3 4a1 1 0 0 1 1-1h3.5a1 1 0 0 1 1 1c0 1.25.2 2.45.57 3.57a1 1 0 0 1-.25 1z"/></svg>
      602-418-5093
    </li>
    <li>
      <svg viewBox="0 0 24 24" aria-hidden="true"><path d="M6 3h10v5H6zM4 9h16a2 2 0 0 1 2 2v7h-4v3H6v-3H2v-7a2 2 0 0 1 2-2zm4 7v3h8v-3z"/></svg>
      602-731-6624
    </li>
    <li>
      <svg viewBox="0 0 24 24" aria-hidden="true"><path d="M2 5h20v14H2zm2 2v.5l8 5 8-5V7l-8 5z"/></svg>
      marisol@vantorelstone.example
    </li>
  </ul>

  <div class="showroom">
    <div class="showroom__label">Vantorel Stone Showroom</div>
    <div>Quillmont Design Center 4183 W Palomar</div>
    <div>Scottsdale AZ</div>
  </div>
</section>

</body>
</html>
```